Web design for a honey company

We are a honey retailing company currently looking for creative design for 3 pages of our existing e-commerce website which can be found here www.alpha.tolvenmarsk.co.nz. The designs need to be responsive i.e. presented in both desktop and mobile versions. We want to use the existing page color pallet, however any fonts can be used. Please use the texts and graphic content in the attachment files provided. For more detailed instructions please. The page does not require coding, the output files should be provided as layered and editable PSD.<br/><br/>Task 2: design 2 home page banners. Images, texts and the concept provided in the "layout structure" file. <br/><br/>The web designs should be presented in both desktop and mobile versions. We are looking for professional designer submissions only!

Target Market(s)

Hi-end consumers
Health conscious consumers

Number of Pages Required

3 page

Requirements
Must have
• 50% of images supplied along + any suggested stock images.
• Supplied texts integrated in the designs.
• Please only use the product images we have provided!
Should not have
• Clipart vector bees, vector honey slots or combs.
• No images of honey in glass jars!
• Do not use images of the traditional honey wooden spoons!
• Do not use images of any other but Manuka flower!

```html
<!DOCTYPE html>
<html lang="en">
<head>
<meta charset="utf-8">
<title>Tolvenmarsk Manuka Honey</title>
<link href="https://fonts.googleapis.com/css2?family=Poppins:wght@300;400;500;600&display=swap" rel="stylesheet">
<style>
:root{
  --gold:#c9a24a;
  --ink:#1f1f1f;
  --text:#555;
  --dark:#232323;
  --paper:#fbfbfb;
  --footer:#1b1b1b;
  --muted:#bdbdbd;
}
*{margin:0;padding:0;box-sizing:border-box}
html,body{width:1200px;height:4342px;overflow:hidden}
body{font-family:'Poppins',sans-serif;background:var(--paper);position:relative;color:var(--ink)}
.abs{position:absolute}
.photo{position:absolute}
.btn-dark{position:absolute;background:var(--dark);color:var(--gold);font-size:15px;font-weight:500;display:flex;align-items:center;justify-content:center;text-transform:uppercase}
.btn-line{position:absolute;border:1.5px solid #ddd;color:#fff;font-size:15px;display:flex;align-items:center;justify-content:center;text-transform:uppercase}
.heading{position:absolute;font-size:22px;font-weight:500;text-transform:uppercase;line-height:36px;border-left:3px solid var(--gold);padding-left:10px;letter-spacing:-.2px}
.para{position:absolute;font-size:13.5px;line-height:28px;color:var(--text);text-align:justify;font-weight:300}
.gold-bar{position:absolute;background:var(--gold)}

.hero{left:0;top:0;width:1200px;height:700px;background:linear-gradient(180deg,#4a4a48 0%,#56544e 45%,#4d4b44 100%);clip-path:polygon(0 0,1200px 0,1200px 650px,600px 692px,0 650px)}
.hero-title{left:110px;top:155px;font-size:32px;line-height:40px;color:#77756f;font-weight:400;text-transform:uppercase}
.hero-sub{left:113px;top:230px;width:480px;font-size:14px;line-height:28px;color:#6d6b66}
.hero-btn{left:112px;top:305px;width:142px;height:50px;background:#413f39;color:#6a5b36;font-size:15px;font-weight:500;display:flex;align-items:center;justify-content:center}
.dots{left:1106px;top:224px}
.dots span{display:block;width:10px;height:10px;border-radius:50%;background:#7c7a75;margin-bottom:6px}
.dots span:first-child{background:#9a9893}
.products-band{left:0;top:690px;width:1200px;height:466px;background:#858585}
.eyebrow{left:0;width:1200px;top:770px;text-align:center;font-size:12px;color:#3b3b3b;text-transform:uppercase}
.band-title{left:0;width:1200px;top:786px;text-align:center;font-size:32px;color:#2a2a2a;font-weight:500;text-transform:uppercase}
.card{position:absolute;top:851px;width:281px;height:305px;border:1px solid #929292;background:#858585}
.card .img{position:absolute;left:70px;top:35px;width:140px;height:135px;border-radius:6px;background:linear-gradient(160deg,#3d3f3c,#2b2d2b)}
.card .name{position:absolute;left:0;width:100%;top:222px;text-align:center;font-size:15px;color:#333}
.card .price{position:absolute;left:0;width:100%;top:250px;text-align:center;font-size:19px;color:#2b2b2b;font-weight:500}
.card .price i{font-style:normal;color:#7a6b3e;font-size:17px;margin-right:6px;letter-spacing:1px}

.nav{left:0;top:1156px;width:1200px;height:71px;background:var(--dark);border-bottom:3px solid var(--gold)}
.nav-item{position:absolute;top:26px;font-size:15px;color:#fff}
.nav-item.on{color:var(--gold)}
.brand{left:528px;top:1164px;width:146px;height:82px;border-radius:50%;background:var(--dark);border:2px solid var(--gold);display:flex;align-items:center;justify-content:center;color:var(--gold);font-size:15px;font-weight:500;letter-spacing:.5px}
.login{left:979px;top:1172px;width:110px;height:38px;background:var(--gold);color:#fff;font-size:16px;font-weight:500;display:flex;align-items:center;justify-content:center}

.band-text{color:#fff}
.footer{left:0;top:4052px;width:1200px;height:290px;background:var(--footer)}
.foot-link{position:absolute;font-size:14px;color:#fff}
.social{position:absolute;top:4114px;width:37px;height:37px;border:1.5px solid #fff;border-radius:50%}
.pay{position:absolute;top:4236px;width:62px;height:26px;border:1px solid #555;border-radius:3px;font-size:11px;font-weight:400;color:var(--muted);display:flex;align-items:center;justify-content:center}
</style>
</head>
<body>

<div class="abs hero" role="img" aria-label="Dimmed hillside landscape at dusk with three jars of manuka honey in the centre"></div>
<div class="photo" role="img" aria-label="Manuka honey jar, left" style="left:488px;top:310px;width:150px;height:300px;border-radius:14px;background:#2a2c2a"></div>
<div class="photo" role="img" aria-label="Manuka honey jar, right" style="left:868px;top:310px;width:150px;height:300px;border-radius:14px;background:#2a2c2a"></div>
<div class="photo" role="img" aria-label="Manuka honey jar, front" style="left:638px;top:225px;width:244px;height:420px;border-radius:18px;background:linear-gradient(180deg,#2e302d,#222422)"></div>
<div class="abs hero-title">The purest manuka honey from<br>the purest environment.</div>
<div class="abs hero-sub">Just New Zealand's unique plant and native bees working in harmony to make the best honey in the world.</div>
<div class="abs hero-btn">SHOP NOW</div>
<div class="abs dots"><span></span><span></span><span></span><span></span></div>

<div class="abs products-band"></div>
<div class="abs eyebrow">Our Products</div>
<div class="abs band-title">Featured Products</div>
<div class="card" style="left:111px"><div class="img" role="img" aria-label="Two manuka honey jars"></div><div class="name">Miele Di Manuka MG100+</div><div class="price"><i>★★★★★</i>USD $18.00</div></div>
<div class="card" style="left:462px"><div class="img" role="img" aria-label="Two manuka honey jars"></div><div class="name">MGO 800+ Manuka Honey</div><div class="price"><i>★★★★★</i>USD $25.00</div></div>
<div class="card" style="left:804px"><div class="img" role="img" aria-label="Two manuka honey jars"></div><div class="name">MGO 500+ Manuka Honey</div><div class="price"><i>★★★★★</i>USD $25.00</div></div>
<div class="abs" style="left:1113px;top:978px"><span style="display:block;width:9px;height:9px;border-radius:50%;background:#8a7440;margin-bottom:7px"></span><span style="display:block;width:9px;height:9px;border-radius:50%;background:#3a3a3a"></span></div>

<div class="abs nav">
  <div class="nav-item on" style="left:111px">Home</div>
  <div class="nav-item" style="left:179px">Shop ⌄</div>
  <div class="nav-item" style="left:254px">MGO Manuka honey ⌄</div>
  <div class="nav-item" style="left:434px">About Us ⌄</div>
  <div class="nav-item" style="left:718px">Contact Us</div>
  <svg class="abs" style="left:836px;top:22px" width="30" height="28" viewBox="0 0 30 28"><path d="M15 26 L3 14 A7 7 0 0 1 15 5 A7 7 0 0 1 27 14 Z" fill="var(--gold)"/><circle cx="25" cy="5" r="5" fill="#fff"/></svg>
  <div class="abs" style="left:896px;top:18px;width:1px;height:34px;background:#555"></div>
  <svg class="abs" style="left:922px;top:20px" width="34" height="30" viewBox="0 0 34 30" fill="none" stroke="var(--gold)" stroke-width="2"><path d="M2 4h5l4 16h16l3-11H9"/><circle cx="13" cy="25" r="2"/><circle cx="25" cy="25" r="2"/><circle cx="27" cy="6" r="5" fill="var(--dark)"/></svg>
</div>
<div class="abs brand">TOLVENMARSK</div>
<div class="abs login">LOGIN</div>

<div class="heading" style="left:111px;top:1322px;width:470px">Tolvenmarsk manuka honey – the purest taste of New Zealand</div>
<div class="para" style="left:111px;top:1402px;width:466px">Tucked away at the edge of the world, New Zealand's natural environment has evolved like no other. Its native plants have been used by the indigenous people of New Zealand for hundreds of years for their healing properties.</div>
<div class="btn-dark" style="left:111px;top:1535px;width:145px;height:50px">Learn More</div>
<div class="gold-bar" style="left:605px;top:1289px;width:8px;height:330px"></div>
<div class="photo" role="img" aria-label="Spoon lifting thick golden manuka honey above an open dark jar" style="left:613px;top:1289px;width:476px;height:330px;background:linear-gradient(135deg,#efeae3 0%,#ddd4c8 55%,#8a5a24 75%,#1c1c1c 100%)"></div>

<div class="photo" role="img" aria-label="Beekeeper in a white suit tending hives in a field surrounded by flying bees" style="left:0;top:1705px;width:1200px;height:435px;background:linear-gradient(100deg,#2b3224 0%,#3f4a32 40%,#8f96a0 70%,#2f3627 100%)"></div>
<svg class="abs" style="left:111px;top:1906px" width="34" height="34" viewBox="0 0 34 34"><circle cx="17" cy="17" r="15" fill="none" stroke="#fff" stroke-width="2"/><path d="M13 10l11 7-11 7z" fill="#fff"/></svg>
<div class="abs band-text" style="left:156px;top:1905px;font-size:24px;font-weight:500">Watch The Harvesting Process Video</div>
<div class="abs" style="left:618px;top:1923px;width:72px;height:2px;background:#fff"></div>
<div class="btn-line" style="left:703px;top:1899px;width:158px;height:50px">Learn More</div>

<div class="photo" role="img" aria-label="White manuka flowers in bloom against a blue sky" style="left:111px;top:2295px;width:184px;height:224px;background:linear-gradient(160deg,#8fb0d8,#e8ece8 50%,#3e5a38)"></div>
<div class="photo" role="img" aria-label="Hive frame covered in bees held by a gloved hand" style="left:295px;top:2224px;width:291px;height:364px;background:linear-gradient(170deg,#222,#6b4a22 45%,#a07a3a 70%,#2a2a2a)"></div>
<div class="gold-bar" style="left:586px;top:2224px;width:7px;height:364px"></div>
<div class="heading" style="left:622px;top:2262px;width:470px">Only the best will do</div>
<div class="para" style="left:622px;top:2316px;width:467px">As any great chef will tell you, the quality of a dish depends on the quality of your ingredients. For our honey, the first ingredient is the Manuka flower. The locations for our hives are carefully chosen by our beekeepers to make sure that the bees have access to the most abundant areas of Manuka plants, giving them the best ingredients to work from to create the best monofloral manuka honey.</div>
<div class="btn-dark" style="left:622px;top:2504px;width:144px;height:50px">Learn More</div>

<div class="photo" role="img" aria-label="Close-up of bees on weathered wood at a hive entrance" style="left:0;top:2671px;width:1200px;height:443px;background:linear-gradient(180deg,#3a2a1c 0%,#6b4a2c 35%,#4a3220 65%,#2a1e14 100%)"></div>
<div class="abs band-text" style="left:0;width:1200px;top:2790px;text-align:center;font-size:29px;font-weight:500;text-transform:uppercase;letter-spacing:-.3px">Protecting our bees</div>
<div class="abs band-text" style="left:170px;width:860px;top:2840px;text-align:center;font-size:13px;line-height:29px;font-weight:300">The proprietary processes our beekeepers use to harvest and extract our Manuka honey are designed to protect our bees. As far as we're concerned, our bees are part of the team and we treat them with respect. That includes minimising our impact on their natural behaviour</div>
<div class="btn-dark" style="left:529px;top:2935px;width:142px;height:50px;background:#2a2018">Learn More</div>

<div class="heading" style="left:111px;top:3271px;width:520px">True MGO certified manuka honey</div>
<div class="para" style="left:111px;top:3325px;width:487px">And finally comes the science part. Tolvenmarsk honey come a long way from the remote locations of New Zealand to your pantry. On its way we make sure every drop of our honey is tested by an independent KLAB-certified laboratory to verify that it has been made using the nectar from the Manuka flower, and is graded according to its Methylglxoal (MGO) content, so you can enjoy the best manuka honey without any compromise.</div>
<div class="btn-dark" style="left:111px;top:3542px;width:145px;height:50px">Learn More</div>
<div class="gold-bar" style="left:645px;top:3200px;width:6px;height:434px"></div>
<div class="photo" role="img" aria-label="Flowering manuka bush under blue sky" style="left:651px;top:3200px;width:213px;height:212px;background:linear-gradient(170deg,#3d7fd0,#e6ebe6 55%,#3a5a34)"></div>
<div class="photo" role="img" aria-label="Mountain lake and hills in New Zealand" style="left:651px;top:3421px;width:213px;height:213px;background:linear-gradient(180deg,#6f95c4,#cfd6dc 30%,#5b6f55 50%,#1f7ab8 70%,#3f6a38)"></div>
<div class="photo" role="img" aria-label="Beekeeper working among blue hive boxes" style="left:874px;top:3225px;width:213px;height:212px;background:linear-gradient(170deg,#4a6a3a,#8a8a7a 45%,#3d6fa8 80%)"></div>
<div class="photo" role="img" aria-label="Open jar of manuka honey viewed from above" style="left:874px;top:3448px;width:213px;height:212px;background:radial-gradient(circle at 50% 50%,#2a2a28 40%,#d8d6d2 42%,#f0efed)"></div>

<div class="photo" role="img" aria-label="Panoramic view over green hills and a harbour" style="left:0;top:3744px;width:1200px;height:308px;background:linear-gradient(180deg,#4a6e92 0%,#6d8aa6 30%,#3f5a3a 60%,#2a3a26 100%)"></div>
<div class="abs band-text" style="left:0;width:1200px;top:3836px;text-align:center;font-size:24px;font-weight:500;text-transform:uppercase;letter-spacing:-.3px">Stay in the loop to find out what's new</div>
<div class="abs" style="left:560px;top:3878px;width:80px;height:2px;background:var(--gold)"></div>
<div class="abs" style="left:389px;top:3906px;width:418px;height:48px;border:1.5px solid #fff;background:rgba(0,0,0,.55)"></div>
<div class="abs" style="left:413px;top:3922px;font-size:13px;color:#fff">Enter Your Email Address</div>
<div class="abs" style="left:687px;top:3906px;width:1.5px;height:48px;background:#fff"></div>
<div class="abs" style="left:688px;top:3921px;width:119px;text-align:center;font-size:15px;color:var(--gold);font-weight:500">SUBMIT</div>

<div class="abs footer"></div>
<div class="abs" style="left:128px;top:4098px;width:202px;height:124px;border-radius:50%;border:2px solid var(--gold);display:flex;align-items:center;justify-content:center;color:var(--gold);font-size:20px;font-weight:500">TOLVENMARSK</div>
<div class="foot-link" style="left:428px;top:4114px">Shop</div>
<div class="foot-link" style="left:428px;top:4142px">Terms &amp; Conditions</div>
<div class="foot-link" style="left:428px;top:4170px">Privacy Policy</div>
<div class="foot-link" style="left:659px;top:4128px">FAQs</div>
<div class="foot-link" style="left:659px;top:4156px">Partnership enquiries</div>
<div class="social" style="left:900px" aria-label="Social profile"></div>
<div class="social" style="left:944px" aria-label="Social profile"></div>
<div class="social" style="left:987px" aria-label="Social profile"></div>
<div class="social" style="left:1030px" aria-label="Social profile"></div>
<div class="pay" style="left:497px">Paywell</div>
<div class="pay" style="left:569px">Cardmax</div>
<div class="pay" style="left:641px">Vantra</div>
<div class="abs" style="left:0;width:1200px;top:4284px;text-align:center;font-size:14px;color:#fff">Copyright © 2020. All Rights Reserved</div>
<svg class="abs" style="left:1144px;top:4227px" width="46" height="46" viewBox="0 0 46 46" fill="none" stroke="var(--gold)" stroke-width="2.5"><path d="M23 3 L41 13 V33 L23 43 L5 33 V13 Z"/><path d="M23 33 V15 M15 22 L23 14 L31 22"/></svg>

</body>
</html>
```